We need a new website design for our company Brindle Forks (https://www.brindleforks.com/). We DO NOT WANT A BORING STANDARD SITE. This site has to be different, and has to POP!

Logo Files: https://files.examplecloud.net/folders/a7Kq3Lm9Zx2Tp8Rw4Vn6Yb1Hc5Jd0Fs

Website Photos here: https://files.examplecloud.net/folders/b3Wm8Qx_T2ngVr7Lp4Ks9Hd6Zc1Ya0Ej

Websites we like:
https://morvenite.sitebloom.io/
http://crunova.com/

We will need the site building Wordpress/Woocommerce and also help with interior pages & installation plug-ins -- see further attachments.

Information about the company:
1. PURPOSE: Why do we exist?
We believe that food is the root source to healthy living.
2. VISION: What future do we want to help create?
A world of healthy and happy people.
3. MISSION: What are we here to do?
Empower every person to utilize food as a means of living a healthy life.

Value Proposition:
Brindle Forks develops new food based on the latest science to provide the human body with the proper nutrients for optimal health. Our research based foods target the key health functions that support healthy aging and active lifestyles. Since 2002, we have been innovating and designing our meals to meet the needs for healthy aging to active lifestyles. To help people perform their best, today & in the future.

Objective:
This is a nationwide issue and it's coming to the surface. Food affects people in a number of different ways. Our objective is to create an approachable and sustainable solution that can assist people with a number of ailments. The end result for all of them is feeling a feeling they haven't felt in quite some time. Feeling a refreshed you. Like water for fish, food for humans. Keep it clean and simple so you can focus on enjoying your life.

PHRASES/TAGLINES:
Empowerment Through Food
Real Food, Real Results
Nutrition Made Simple
Not Just Meal Prep, Food Science
A healthier you, delivered to your door
Increase your health and wellness baseline.
Discover the potential of healthier eating
Become the best version of you
It’s incredible what proper nutrition feels like
Taste & feel the difference. Your future self will thank you.
A healthier you is just a meal away
Life Changing results
Overwhelmed with being healthy, stops here.
Designed by doctors, approved by humans
Results Driven Healthy Eating, Delivered to you.
Become the person you deserve to be.
Enjoy the process of becoming a better you

Value Propositions:
We Educate & Empower People Through Food to Live Their Best Life
Sustainable health through proper nutrition… that’s enjoyable too.

Key Statements:
We provide satisfying meals that are nutrient dense & deliver results.
Our meals provide an easy way to enjoy an anti-inflammatory diet that's as satisfying as it is healthy.
Health, fat loss & feeling good through chef-prepared, nutrient-dense, satisfying meals delivered to your door.

PLEASE REVIEW THE ATTACHMENTS.

Industry/Entity Type

See Description & Attachments

Coding

Coded - Design and coding required

Number of Pages Required

5+ page

Font styles to use
Other font styles liked:
• See Description & Attachments

Colors
0094D4
00A9DD
6FCCEA
C7EBF8
E9F6FB
00AB8E
00BBA5
67D7C9
C6EFE9
E9F9F6

Requirements
Must have
Nice to have
Should not have

```html
<!DOCTYPE html>
<html lang="en">
<head>
<meta charset="utf-8">
<title>Brindle Forks — Eat Better. Live Better.</title>
<link href="https://fonts.googleapis.com/css2?family=Josefin+Sans:wght@400;600;700&family=Montserrat:wght@400;500;600;700&display=swap" rel="stylesheet">
<style>
:root{
  --ink:#1b1b1b;
  --muted:#555;
  --brand:#0e5546;
  --menu-bg:#125f4d;
  --value-bg:#2c4a2c;
  --sage:#a9c09e;
  --sage-light:#dfe8da;
  --leaf:#86ad72;
  --night:#161616;
  --white:#fff;
  --head:'Josefin Sans',sans-serif;
  --body:'Montserrat',sans-serif;
}
*{box-sizing:border-box;margin:0;padding:0}
html,body{width:1200px;height:4199px;overflow:hidden}
body{position:relative;background:var(--white);font-family:var(--body);color:var(--ink)}
.abs{position:absolute}
a{color:inherit;text-decoration:none}
.btn{position:absolute;display:flex;align-items:center;justify-content:center;border-radius:30px;font-family:var(--body);font-weight:700;letter-spacing:1.5px;font-size:11px;text-transform:uppercase}
.btn-dark{background:var(--brand);color:var(--white)}
.btn-light{background:var(--white);color:var(--brand)}
.center{text-align:center;left:0;width:1200px}

/* header */
.hero-swoosh{left:-260px;top:-330px;width:970px;height:970px;border-radius:50%;background:var(--sage-light)}
.hero-swoosh-cut{left:-80px;top:-200px;width:760px;height:760px;border-radius:50%;background:var(--white)}
.brand-name{left:62px;top:40px;font-family:var(--head);font-weight:700;font-size:30px;color:var(--brand);line-height:1}
.brand-tag{left:70px;top:110px;font-size:9px;letter-spacing:3px;color:var(--brand);font-weight:600}
.auth{left:930px;top:14px;font-size:10px;color:var(--ink)}
.auth span{color:var(--leaf)}
.head-icons{left:1048px;top:10px;display:flex;gap:14px}
.nav{left:755px;top:58px;display:flex;gap:27px;font-size:12px;font-weight:500}
.search{left:1098px;top:51px;width:31px;height:31px;border-radius:50%;background:var(--brand);display:flex;align-items:center;justify-content:center}

/* hero */
.plate{border-radius:50%;box-shadow:0 10px 30px rgba(0,0,0,.18)}
.hero-plate{left:218px;top:182px;width:380px;height:380px;background:radial-gradient(circle,#9aa35c 0 34%,#d4c38e 45%,#f6f6f3 52%,#ffffff 100%)}
.hero-top-plate{left:535px;top:-60px;width:175px;height:135px;border-radius:0 0 90px 90px;background:radial-gradient(circle at 50% 20%,#7d9a55 0 25%,#fafafa 40%)}
.hero-kicker{left:633px;top:148px;font-family:var(--head);font-size:31px}
.hero-title{left:632px;top:195px;font-family:var(--head);font-weight:700;font-size:77px;line-height:83px;letter-spacing:1px}
.hero-copy{left:650px;top:374px;width:490px;font-size:13.5px;line-height:23px}
.slider-dots{display:flex;gap:5px}
.slider-dots i{display:block;width:6px;height:6px;border-radius:50%;background:#222}
.slider-dots i:first-child{background:var(--sage)}

/* welcome */
.welcome-kicker{top:636px;font-family:var(--head);font-size:20px}
.welcome-title{top:662px;font-family:var(--head);font-weight:700;font-size:43px;letter-spacing:1px}
.welcome-copy{top:729px;left:180px;width:840px;text-align:center;font-size:13px;line-height:23px;color:#333}
.side-plate{left:1040px;top:770px;width:220px;height:220px;background:radial-gradient(circle,#6b4a3a 0 22%,#5d8a3f 34%,#f5f5f2 48%,#fff)}

/* menu */
.menu{left:0;top:939px;width:1200px;height:482px;background:var(--menu-bg);overflow:hidden}
.menu-title{top:58px;font-family:var(--head);font-weight:700;font-size:40px;color:var(--white);letter-spacing:1px}
.menu-tabs{top:132px;left:250px;width:700px;display:flex;justify-content:space-between;color:var(--white);font-size:18px;font-weight:500}
.menu-tabs span{display:flex;align-items:center;gap:6px}
.card{top:186px;width:247px;height:218px}
.card-photo{position:absolute;left:0;top:0;width:247px;height:150px;border-radius:8px;background:linear-gradient(90deg,#8a5a38,#b47d52 12%,#f4f4f2 20%,#ffffff 50%,#f4f4f2 80%,#a66f45 88%,#7d5033)}
.card-photo i{position:absolute;left:50%;top:14px;width:100px;height:90px;margin-left:-50px;border-radius:50%;background:radial-gradient(circle,#c4693a 0 30%,#5e8e3c 55%,transparent 72%)}
.card-info{position:absolute;left:24px;top:133px;width:199px;height:85px;background:var(--white);border-radius:0 0 8px 8px;text-align:center;padding-top:15px}
.card-info b{display:block;font-weight:500;font-size:13px;letter-spacing:.5px}
.card-info small{display:block;font-size:10px;margin-top:7px;color:#333}
.card .btn{left:73px;top:202px;width:101px;height:33px;background:var(--sage);color:var(--white);font-size:10px}

/* audience */
.who-title{top:1493px;font-family:var(--head);font-weight:700;font-size:40px;letter-spacing:1px}
.who{top:1580px;width:260px;text-align:center}
.who svg{display:block;margin:0 auto}
.who h3{margin-top:18px;font-family:var(--head);font-weight:700;font-size:22px;letter-spacing:.5px}
.who h3 span{color:var(--leaf)}
.who p{margin-top:10px;font-size:11px;line-height:19px;color:#333}

/* value */
.value{left:0;top:1814px;width:1200px;height:533px;background:linear-gradient(110deg,#22401f,#2f5030 60%,#24411f)}
.photo-frame{border:5px solid var(--white);box-shadow:0 6px 18px rgba(0,0,0,.3)}
.value-photo-a{left:72px;top:136px;width:298px;height:344px;background:linear-gradient(135deg,#6a5140,#c99d6a 40%,#5e3d30 70%,#3b2a22)}
.value-photo-b{left:313px;top:52px;width:300px;height:344px;background:radial-gradient(circle,#d14d2c 0 20%,#1d1d1d 34%,#2a2a2a 42%,#d3a76b 46%,#e7c08a 100%)}
.value-title{left:701px;top:108px;font-family:var(--head);font-weight:700;font-size:40px;color:var(--white);letter-spacing:1px}
.value-copy{left:701px;top:187px;width:430px;font-size:12.5px;line-height:22.5px;color:var(--white)}

/* pillars */
.pillar{top:2347px;width:400px;height:268px;color:var(--white);text-align:center;display:flex;flex-direction:column;align-items:center;justify-content:flex-end;padding-bottom:36px}
.pillar h4{font-weight:700;font-size:16px;letter-spacing:1px}
.pillar em{font-style:normal;font-size:11px;color:#b7d69a;margin-top:4px;letter-spacing:.3px}
.pillar p{font-size:11px;margin-top:14px;max-width:290px;line-height:16px}

/* testimonials */
.say-title{top:2688px;font-family:var(--head);font-weight:700;font-size:40px;letter-spacing:1px}
.say-band{left:267px;top:2763px;width:660px;height:349px;background:var(--sage)}
.quote{top:2817px;width:336px;height:240px;background:var(--white);border-radius:20px;padding:44px 27px 0 27px}
.quote.lift{box-shadow:0 8px 26px rgba(0,0,0,.15)}
.quote p{font-size:12px;line-height:21px;color:#333}
.quote .who-line{margin-top:26px;display:flex;align-items:center;gap:12px;font-size:14px}
.stars{color:#f0b31a;font-size:14px;letter-spacing:2px}
.quote small{display:block;font-size:10px;color:#444;margin-top:2px}
.say-dots{left:585px;top:3084px;display:flex;gap:4px}
.say-dots i{width:6px;height:6px;border-radius:50%;background:#555;display:block}
.say-dots i:first-child{background:var(--white)}

/* newsletter */
.news{left:0;top:3190px;width:1200px;height:342px;background:linear-gradient(120deg,#1b1b1b,#3a3a38 35%,#222 60%,#3d3d3a 85%,#1c1c1c)}
.news-kicker{top:104px;font-family:var(--head);font-size:20px;color:var(--white)}
.news-title{top:130px;font-family:var(--head);font-weight:700;font-size:40px;color:var(--white);letter-spacing:1px}
.news-field{left:323px;top:197px;width:554px;height:45px;border-radius:30px;background:var(--white);display:flex;align-items:center;padding-left:27px;font-size:11px}
.news-field .btn{right:4px;top:4px;width:127px;height:37px;font-size:11px;letter-spacing:.5px}

/* awards */
.award-title{top:3606px;font-family:var(--head);font-weight:700;font-size:40px;letter-spacing:1px}
.stat{top:3694px;width:300px;text-align:center}
.stat b{display:block;font-family:var(--head);font-weight:700;font-size:42px;color:var(--sage)}
.stat span{display:block;font-size:15px;color:#333;margin-top:2px}

/* footer */
.footer{left:0;top:3832px;width:1200px;height:367px;background:var(--night);color:var(--white)}
.f-brand{left:72px;top:70px;font-family:var(--head);font-weight:700;font-size:26px;color:var(--white);line-height:1}
.f-tag{left:72px;top:135px;font-size:8px;letter-spacing:3px;font-weight:600}
.socials{left:72px;top:180px;display:flex;gap:12px}
.socials i{display:block;width:25px;height:25px;border-radius:50%;background:var(--brand)}
.f-col{top:60px}
.f-col h5{font-family:var(--head);font-weight:700;font-size:18px;color:var(--sage);margin-bottom:16px;letter-spacing:.5px}
.f-col li{list-style:none;font-size:10.5px;line-height:24px}
.contact-row{display:flex;align-items:flex-start;gap:10px;font-size:10.5px;line-height:14px;margin-bottom:22px}
.contact-row i{flex:none;width:23px;height:23px;border-radius:50%;background:var(--brand);display:flex;align-items:center;justify-content:center}
.copy{top:4134px;font-size:10px;color:#aaa}
.copy span{color:var(--sage)}
</style>
</head>
<body>

<!-- header & hero -->
<div class="abs hero-swoosh"></div>
<div class="abs hero-swoosh-cut"></div>
<div class="abs plate hero-top-plate" role="img" aria-label="Top of a plated salad"></div>

<a class="abs brand-name" href="https://www.brindleforks.com/">Brindle Forks</a>
<div class="abs brand-tag">EAT BETTER. LIVE BETTER.</div>

<div class="abs auth"><span>Login</span> | Register</div>
<div class="abs head-icons">
  <svg width="17" height="17" viewBox="0 0 24 24" fill="none" stroke="#222" stroke-width="1.8"><circle cx="12" cy="8" r="4"/><path d="M4 21c1-5 15-5 16 0"/></svg>
  <svg width="17" height="17" viewBox="0 0 24 24" fill="none" stroke="#222" stroke-width="1.8"><path d="M12 20s-8-5-8-11a4 4 0 0 1 8-1 4 4 0 0 1 8 1c0 6-8 11-8 11z"/></svg>
  <svg width="17" height="17" viewBox="0 0 24 24" fill="none" stroke="#222" stroke-width="1.8"><path d="M2 3h3l3 12h11l2-8H7"/><circle cx="9" cy="20" r="1.5"/><circle cx="18" cy="20" r="1.5"/></svg>
</div>
<nav class="abs nav"><a>Shop Now</a><a>About</a><a>Menu</a><a>Programs</a><a>FAQ</a></nav>
<div class="abs search"><svg width="13" height="13" viewBox="0 0 24 24" fill="none" stroke="#fff" stroke-width="2.4"><circle cx="10" cy="10" r="7"/><path d="M15 15l6 6"/></svg></div>

<div class="abs plate hero-plate" role="img" aria-label="Plated salad with tomatoes, red onion, greens and seasoned ground meat"></div>
<div class="abs hero-kicker">Weekly</div>
<h1 class="abs hero-title">CUSTOMIZED<br>ORDERING</h1>
<p class="abs hero-copy">We provide a sustainable diet &amp; nutritional support that empowers you to live your best life</p>
<a class="btn btn-dark" style="left:651px;top:447px;width:130px;height:39px">Order Now</a>
<div class="abs slider-dots" style="left:1097px;top:531px"><i></i><i></i><i></i></div>

<!-- welcome -->
<div class="abs center welcome-kicker">Welcome To</div>
<h2 class="abs center welcome-title">Brindle Forks</h2>
<p class="abs welcome-copy">As we already know, if you are NOT currently living a Healthy lifestyle, becoming healthy is not something that happens overnight. Not to mention, as humans we are similar, but ALL different. Due to the fact that there is a such a HUGE NEED for a One Stop Wellness Shop, in YOUR AREA!</p>
<a class="btn btn-dark" style="left:535px;top:820px;width:130px;height:39px">Read More</a>
<div class="abs plate side-plate" role="img" aria-label="Plate of sliced steak with roasted vegetables"></div>

<!-- menu -->
<section class="abs menu">
  <h2 class="abs center menu-title">Our Menu</h2>
  <div class="abs menu-tabs">
    <span><svg width="18" height="18" viewBox="0 0 24 24" fill="none" stroke="#fff" stroke-width="1.6"><circle cx="12" cy="12" r="8"/><path d="M8 12h8"/></svg>BEEF</span>
    <span><svg width="18" height="18" viewBox="0 0 24 24" fill="none" stroke="#fff" stroke-width="1.6"><circle cx="9" cy="9" r="5"/><path d="M13 13l7 7"/></svg>CHICKEN</span>
    <span><svg width="18" height="18" viewBox="0 0 24 24" fill="none" stroke="#fff" stroke-width="1.6"><rect x="4" y="6" width="16" height="12" rx="2"/></svg>SEA FOOD</span>
    <span><svg width="18" height="18" viewBox="0 0 24 24" fill="none" stroke="#fff" stroke-width="1.6"><path d="M3 18h18M6 18c0-6 12-6 12 0"/></svg>TURKEY</span>
    <span><svg width="18" height="18" viewBox="0 0 24 24" fill="none" stroke="#fff" stroke-width="1.6"><circle cx="12" cy="13" r="7"/><path d="M12 6V3"/></svg>VEGGIE</span>
  </div>
  <div class="abs card" style="left:72px"><div class="card-photo" role="img" aria-label="Beef entree on a white plate"><i></i></div><div class="card-info"><b>ENTREES BEEF</b><small>Sed ut perspiciatis unde omnis</small></div><a class="btn">Order Now</a></div>
  <div class="abs card" style="left:341px"><div class="card-photo" role="img" aria-label="Chicken entree with salad on a white plate"><i></i></div><div class="card-info"><b>ENTREES CHICKEN</b><small>Sed ut perspiciatis unde omnis</small></div><a class="btn">Order Now</a></div>
  <div class="abs card" style="left:611px"><div class="card-photo" role="img" aria-label="Salmon with asparagus and cauliflower on a white plate"><i></i></div><div class="card-info"><b>ENTREES SEAFOOD</b><small>Sed ut perspiciatis unde omnis</small></div><a class="btn">Order Now</a></div>
  <div class="abs card" style="left:880px"><div class="card-photo" role="img" aria-label="Turkey with roasted vegetables on a white plate"><i></i></div><div class="card-info"><b>ENTREES TURKEY</b><small>Sed ut perspiciatis unde omnis</small></div><a class="btn">Order Now</a></div>
</section>

<!-- audience -->
<h2 class="abs center who-title">Who is Brindle Forks For?</h2>
<div class="abs who" style="left:64px">
  <svg width="60" height="50" viewBox="0 0 60 50" fill="none" stroke="#222" stroke-width="2"><path d="M30 46S6 32 6 16a12 12 0 0 1 24-4 12 12 0 0 1 24 4c0 16-24 30-24 30z"/><path d="M10 24h12l4-8 5 14 4-6h10" stroke="#86ad72"/><circle cx="50" cy="8" r="5" stroke="#86ad72"/></svg>
  <h3>General <span>Health</span></h3>
  <p>You need the support of a healthy diet to get back in shape and improve your overall health.</p>
</div>
<div class="abs who" style="left:335px">
  <svg width="50" height="50" viewBox="0 0 50 50" fill="none" stroke="#222" stroke-width="2"><circle cx="25" cy="14" r="9"/><path d="M25 23v14M12 37h26M12 37v4M25 37v4M38 37v4"/><circle cx="12" cy="44" r="2.5" stroke="#86ad72"/><circle cx="25" cy="44" r="2.5" stroke="#86ad72"/><circle cx="38" cy="44" r="2.5" stroke="#86ad72"/></svg>
  <h3>Business <span>Individuals</span></h3>
  <p>You need the support of a healthy diet to get back in shape and improve your overall health.</p>
</div>
<div class="abs who" style="left:604px">
  <svg width="50" height="50" viewBox="0 0 50 50" fill="none" stroke="#222" stroke-width="2"><path d="M8 8h34M14 5v6M36 5v6"/><circle cx="25" cy="15" r="4"/><path d="M15 10l10 10 10-10M25 20v12M25 32l-7 14M25 32l7 14"/></svg>
  <h3>Fitness <span>Enthusiasts</span></h3>
  <p>You need the support of a healthy diet to get back in shape and improve your overall health.</p>
</div>
<div class="abs who" style="left:874px">
  <svg width="50" height="50" viewBox="0 0 50 50" fill="none" stroke="#222" stroke-width="2"><circle cx="34" cy="7" r="3"/><path d="M30 12L18 26l12 4-6 16M18 26L8 40M30 12l8 10" /><path d="M10 22c6-2 10 0 14 4" stroke="#86ad72"/></svg>
  <h3>Professional <span>Athletes</span></h3>
  <p>You need the support of a healthy diet to get back in shape and improve your overall health.</p>
</div>

<!-- value proposition -->
<section class="abs value">
  <div class="abs photo-frame value-photo-a" role="img" aria-label="Braised beef with caramelized onion and rice"></div>
  <div class="abs photo-frame value-photo-b" role="img" aria-label="Bowl of tomato quinoa with herbs on a wooden board"></div>
  <h2 class="abs value-title">Value Proposition</h2>
  <p class="abs value-copy">Brindle Forks develops new food based on the latest science to provide the human body with the proper nutrients for optimal health. Our research based foods target the key health functions that support healthy aging and active lifestyles. Since 2002, we have been innovating and designing our meals to meet the needs for healthy aging to active lifestyles. To help people perform their best, today &amp; in the future.</p>
  <a class="btn btn-light" style="left:701px;top:376px;width:130px;height:39px">Read More</a>
</section>

<!-- pillars -->
<div class="abs pillar" style="left:0;background:linear-gradient(rgba(0,0,0,.35),rgba(0,0,0,.55)),linear-gradient(135deg,#7c8c4a,#c9a24f 45%,#4f6a2e)" role="img" aria-label="Vegetable frittata">
  <h4>PURPOSE</h4><em>WHY DO WE EXIST?</em><p>We believe that food is the root source to healthy living.</p>
</div>
<div class="abs pillar" style="left:400px;background:linear-gradient(rgba(0,0,0,.35),rgba(0,0,0,.55)),linear-gradient(135deg,#3c3a34,#8d6d4d 45%,#2f2d29)" role="img" aria-label="Sliced roast with berries on slate">
  <h4>VISION</h4><em>WHAT FUTURE DO WE WANT TO HELP CREATE?</em><p>What future do we want to help create?</p>
</div>
<div class="abs pillar" style="left:800px;background:linear-gradient(rgba(0,0,0,.3),rgba(0,0,0,.5)),linear-gradient(135deg,#b7893d,#e1c48a 45%,#9a6f35)" role="img" aria-label="Roasted chicken with sweet potato">
  <h4>MISSION</h4><em>WHAT ARE WE HERE TO DO?</em><p>Empower every person to utilize food as a means of living a healthy life.</p>
</div>

<!-- testimonials -->
<h2 class="abs center say-title">What Others Are Saying</h2>
<div class="abs say-band"></div>
<div class="abs quote" style="left:73px">
  <p>Sed ut perspiciatis unde omnis iste natus error sit voluptatem accusantium doloremque laudantium, totam rem aperiam, eaque ipsa quae ab illo inventore veritatis et quasi architecto beatae vitae dicta sunt explicabo.</p>
  <div class="who-line"><div>Owen Halvard<small>Freelancer</small></div><span class="stars">★★★★★</span></div>
</div>
<div class="abs quote lift" style="left:431px">
  <p>Sed ut perspiciatis unde omnis iste natus error sit voluptatem accusantium doloremque laudantium, totam rem aperiam, eaque ipsa quae ab illo inventore veritatis et quasi architecto beatae vitae dicta sunt explicabo.</p>
  <div class="who-line"><div>Tessa Morrow<small>Freelancer</small></div><span class="stars">★★★★★</span></div>
</div>
<div class="abs quote" style="left:791px">
  <p>Sed ut perspiciatis unde omnis iste natus error sit voluptatem accusantium doloremque laudantium, totam rem aperiam, eaque ipsa quae ab illo inventore veritatis et quasi architecto beatae vitae dicta sunt explicabo.</p>
  <div class="who-line"><div>Rafael Quint<small>Freelancer</small></div><span class="stars">★★★★★</span></div>
</div>
<div class="abs say-dots"><i></i><i></i><i></i></div>

<!-- newsletter -->
<section class="abs news" role="img" aria-label="Dark tabletop with grill rack, herbs and plates">
  <div class="abs center news-kicker">Subscribe To</div>
  <h2 class="abs center news-title">Our Nesletter</h2>
  <div class="abs news-field">Enter Your Email:<a class="btn btn-dark">Subscribe</a></div>
</section>

<!-- awards -->
<h2 class="abs center award-title">Award Winning Meals</h2>
<div class="abs stat" style="left:44px"><b>150K</b><span>HAPPY CLIENTS</span></div>
<div class="abs stat" style="left:314px"><b>500K</b><span>MEALS SERVED NATION WIDE</span></div>
<div class="abs stat" style="left:584px"><b>35+</b><span>CHEF PREPARED MEALS</span></div>
<div class="abs stat" style="left:854px"><b>215</b><span>AWARDS</span></div>

<!-- footer -->
<footer class="abs footer">
  <div class="abs f-brand">Brindle Forks</div>
  <div class="abs f-tag">EAT BETTER. LIVE BETTER</div>
  <div class="abs socials"><i></i><i></i><i></i></div>

  <div class="abs f-col" style="left:341px"><h5>Quick Links</h5><ul><li>Shop Now</li><li>About</li><li>Menu</li><li>Programs</li><li>FAQ</li><li>Contact Us</li></ul></div>
  <div class="abs f-col" style="left:521px"><h5>Others Link</h5><ul><li>My Account</li><li>Shipping &amp; Return</li><li>All Products</li><li>Gift Certificate</li></ul></div>
  <div class="abs f-col" style="left:723px"><h5>Others Link</h5><ul><li>Vie Cart</li><li>Corporate catering</li><li>Podcast</li><li>Become Affiliated</li></ul></div>
  <div class="abs f-col" style="left:928px"><h5>Contact Us</h5>
    <div class="contact-row"><i><svg width="10" height="12" viewBox="0 0 24 24" fill="#fff"><path d="M12 2a7 7 0 0 0-7 7c0 5 7 13 7 13s7-8 7-13a7 7 0 0 0-7-7zm0 10a3 3 0 1 1 0-6 3 3 0 0 1 0 6z"/></svg></i><span>14/2 Lorem ipsum dolar sit amet<br>Lorem 254U UKE</span></div>
    <div class="contact-row"><i><svg width="11" height="11" viewBox="0 0 24 24" fill="#fff"><path d="M6 2l4 5-2 3a12 12 0 0 0 6 6l3-2 5 4-2 4C10 22 2 14 2 4z"/></svg></i><span style="padding-top:5px">855-410-2287</span></div>
    <div class="contact-row"><i><svg width="11" height="9" viewBox="0 0 24 18" fill="#fff"><path d="M0 0h24v18H0z" fill="none"/><path d="M1 1h22v16H1zM1 1l11 9 11-9" fill="#fff" stroke="#0e5546" stroke-width="1.5"/></svg></i><span style="padding-top:5px">hello@brindleforks.com</span></div>
  </div>
</footer>
<div class="abs center copy">Copyright © 2022 <span>Brindle Forks</span>. All Rights Reserved.</div>

</body>
</html>
```